Road Construction Company needs business cards

We would like a new business card designed for our business.

We're a road construction company based in Qld, Australia.

Can the business card please have the following information on it.

Name: Warren Halbeck
Position: General Manager
Phone: 0472 915 348
Email: Warren.halbeck@tovrin.com.au
Address: 87 Marrow Ave, Pendlebay, QLD, 4023
Website: www.tovrin.com.au

Visually we'd like the card to be professional and simple.

Attached is our logo.

Our website is www.tovrin.com.au

Target Market(s)

Men aged 25-60

Contact Information for Business Card

As listed in project description

Font styles to use
Serif

Requirements
Must have
• Large logo on back of card

```html
<!DOCTYPE html>
<html lang="en">
<head>
<meta charset="utf-8">
<title>Tovrin Business Card</title>
<link rel="stylesheet" href="https://fonts.googleapis.com/css2?family=Poppins:wght@400;600;700&display=swap">
<style>
  :root {
    --backdrop: #404040;
    --card-white: #fbfbfb;
    --brand-navy: #1a55a6;
    --brand-sky: #3fa7d9;
    --text-grey: #4a4a4a;
    --photo-deep: #0d2a5c;
    --photo-mid: #0e4a9c;
    --photo-dark: #15213d;
  }
  * { box-sizing: border-box; margin: 0; padding: 0; }
  html, body {
    width: 1200px; height: 801px; overflow: hidden;
    background: var(--backdrop);
    font-family: "Poppins", sans-serif;
  }
  .canvas {
    width: 1200px; height: 801px;
    display: flex; align-items: center; justify-content: center; gap: 40px;
  }
  .card {
    position: relative;
    width: 540px; height: 330px;
    overflow: hidden;
    box-shadow: 0 14px 30px rgba(0,0,0,.35);
  }
  .card-front { background: var(--card-white); }
  .front-shapes { position: absolute; inset: 0; width: 100%; height: 100%; }
  .front-content { position: absolute; left: 44px; top: 70px; }
  .brand-name {
    font-weight: 700; color: var(--brand-navy);
    font-size: 40px; letter-spacing: 1px; line-height: 1;
  }
  .person-name {
    margin-top: 22px;
    font-weight: 700; color: var(--brand-navy);
    font-size: 21px; line-height: 1.1;
  }
  .person-role {
    font-weight: 400; color: var(--brand-sky);
    font-size: 16px; line-height: 1.3;
  }
  .rule {
    width: 30px; height: 2px; background: var(--brand-sky);
    margin: 12px 0 10px;
  }
  .details { list-style: none; color: var(--text-grey); font-size: 12.5px; line-height: 1.5; }
  .details li { display: flex; align-items: center; gap: 7px; }
  .details .address { padding-left: 0; }
  .icon { width: 11px; height: 11px; fill: var(--brand-navy); flex: none; }
  .card-back {
    background: var(--photo-deep);
  }
  .back-photo {
    position: absolute; inset: 0;
    background:
      radial-gradient(ellipse at 20% 75%, var(--photo-mid) 0%, rgba(14,74,156,0) 60%),
      linear-gradient(135deg, var(--photo-mid) 0%, var(--photo-deep) 55%, var(--photo-dark) 100%);
  }
  .back-brand {
    position: absolute; left: 0; right: 0; top: 50%;
    transform: translateY(-50%);
    text-align: center;
    font-weight: 700; color: #ffffff;
    font-size: 64px; letter-spacing: 3px; line-height: 1;
  }
</style>
</head>
<body>
<main class="canvas">
  <section class="card card-front" aria-label="Business card front">
    <svg class="front-shapes" viewBox="0 0 540 330" preserveAspectRatio="none" aria-hidden="true">
      <polygon points="330,0 540,0 540,170 395,130" fill="var(--brand-navy)"/>
      <polygon points="540,170 540,330 430,330 440,205" fill="var(--brand-sky)"/>
    </svg>
    <div class="front-content">
      <div class="brand-name">TOVRIN</div>
      <div class="person-name">Warren Halbeck</div>
      <div class="person-role">General Manager</div>
      <div class="rule"></div>
      <ul class="details">
        <li class="address">87 Marrow Ave,</li>
        <li class="address">Pendlebay, QLD, 4023</li>
        <li>
          <svg class="icon" viewBox="0 0 24 24" aria-hidden="true"><path d="M6.6 10.8a15.1 15.1 0 0 0 6.6 6.6l2.2-2.2a1 1 0 0 1 1-.25 11.4 11.4 0 0 0 3.6.57 1 1 0 0 1 1 1V20a1 1 0 0 1-1 1A17 17 0 0 1 3 4a1 1 0 0 1 1-1h3.5a1 1 0 0 1 1 1c0 1.25.2 2.45.57 3.57a1 1 0 0 1-.25 1z"/></svg>
          0472 915 348
        </li>
        <li>
          <svg class="icon" viewBox="0 0 24 24" aria-hidden="true"><path d="M2 5h20v14H2z M2 5l10 8 10-8" /></svg>
          Warren.halbeck@tovrin.com.au
        </li>
        <li>
          <svg class="icon" viewBox="0 0 24 24" aria-hidden="true"><circle cx="12" cy="12" r="10"/></svg>
          www.tovrin.com.au
        </li>
      </ul>
    </div>
  </section>

  <section class="card card-back" aria-label="Business card back">
    <div class="back-photo" role="img" aria-label="Blue-toned photograph of a road roller compacting fresh asphalt"></div>
    <div class="back-brand">TOVRIN</div>
  </section>
</main>
</body>
</html>
```